Kor'v Meridell Travel

We need a sleek, professional, inviting card to elicit global travel for the experienced and professional traveler. Royal blue, black and silver. (perhaps the wording could be silver with black shadow?-get creative) Maybe a watermark on the front and the full raised logo on the back.
We want a stylish and modern card, but professional.

```html
<!DOCTYPE html>
<html lang="en">
<head>
<meta charset="utf-8">
<title>Kor'v Meridell Travel — Business Card</title>
<link href="https://fonts.googleapis.com/css2?family=Open+Sans:ital,wght@0,400;0,700;0,800;1,400&display=swap" rel="stylesheet">
<style>
  :root {
    --page: #2a2a2a;
    --card: #1f1f20;
    --royal: #1fa3e0;
    --lime: #7cc242;
    --silver: #b9bcc0;
    --text-grey: #c8c8c8;
    --muted: #9a9a9a;
  }
  * { margin: 0; padding: 0; box-sizing: border-box; }
  html, body {
    width: 1200px; height: 900px; overflow: hidden;
    background: var(--page);
    font-family: "Open Sans", Arial, sans-serif;
  }
  .canvas {
    position: relative; width: 1200px; height: 900px;
    display: flex; flex-direction: column; align-items: center; justify-content: center; gap: 48px;
  }
  .card {
    position: relative; width: 640px; height: 366px;
    background: var(--card);
    box-shadow: 0 18px 40px rgba(0,0,0,.55);
  }
  /* Front */
  .holder { position: absolute; left: 44px; top: 50px; }
  .holder__name {
    color: var(--royal); font-weight: 800; font-size: 23px;
    letter-spacing: .5px; text-transform: uppercase; line-height: 1.1;
  }
  .holder__title { color: var(--muted); font-size: 15px; margin-top: 2px; }
  .divider {
    position: absolute; left: 44px; right: 44px; top: 124px;
    height: 1px; background: var(--royal);
  }
  .contacts { position: absolute; left: 44px; top: 146px; list-style: none; }
  .contacts li {
    display: flex; align-items: center; gap: 9px;
    color: var(--text-grey); font-size: 14px; line-height: 24px;
  }
  .contacts svg { width: 12px; height: 12px; flex: none; }
  .brand {
    position: absolute; right: 44px; top: 56px;
    display: flex; align-items: center; gap: 10px;
  }
  .brand__dot { width: 12px; height: 12px; border-radius: 50%; background: var(--lime); }
  .brand__name {
    color: var(--royal); font-weight: 700; font-size: 19px;
    text-transform: uppercase; letter-spacing: 1px;
  }
  .address {
    position: absolute; right: 44px; bottom: 40px; text-align: right;
    color: var(--text-grey); font-size: 15px; line-height: 22px;
  }
  /* Back */
  .card--back { display: flex; align-items: center; justify-content: center; }
  .back-name {
    color: var(--silver); font-weight: 800; font-size: 38px;
    text-transform: uppercase; letter-spacing: 2px;
  }
</style>
</head>
<body>
<main class="canvas">
  <section class="card card--front" aria-label="Card front">
    <div class="holder">
      <p class="holder__name">Daren Holloway</p>
      <p class="holder__title">President</p>
    </div>
    <div class="brand">
      <span class="brand__name">Kor'v Meridell Travel</span>
      <span class="brand__dot"></span>
    </div>
    <div class="divider"></div>
    <ul class="contacts">
      <li>
        <svg viewBox="0 0 12 12" aria-hidden="true"><path d="M2.5 1h2l1 3-1.3 1a6 6 0 0 0 2.8 2.8l1-1.3 3 1v2c0 .6-.5 1.2-1.2 1.2A10 10 0 0 1 1.3 2.2C1.3 1.5 1.9 1 2.5 1z" fill="#7cc242"/></svg>
        949-555-0187
      </li>
      <li>
        <svg viewBox="0 0 12 12" aria-hidden="true"><rect x="0.5" y="2" width="11" height="8" fill="#7cc242"/><path d="M0.5 2.5 6 6.5l5.5-4" stroke="#1f1f20" stroke-width="1" fill="none"/></svg>
        info@korvmeridell.com
      </li>
      <li>
        <svg viewBox="0 0 12 12" aria-hidden="true"><circle cx="6" cy="6" r="5.2" fill="none" stroke="#7cc242" stroke-width="1.3"/><path d="M.8 6h10.4M6 .8c-2.4 2.8-2.4 7.6 0 10.4M6 .8c2.4 2.8 2.4 7.6 0 10.4" stroke="#7cc242" stroke-width="1" fill="none"/></svg>
        www.korvmeridell.com
      </li>
    </ul>
    <address class="address" style="font-style:normal">
      18420 Harbor Crest Way<br>
      Seacliff Bay CA 92600
    </address>
  </section>

  <section class="card card--back" aria-label="Card back">
    <span class="back-name">Kor'v Meridell Travel</span>
  </section>
</main>
</body>
</html>
```